Personal Chef Business Card Design

My company, Simmered, is a personal in-home chef service that caters to clients' needs, but I am not a caterer. The types of services that I provide range from : weekly menus for busy families, special menus for specific diets, custom menus, private parties, intimate dinners, and brunch parties. My cooking style is seasonal and simple with the option of a variety of cuisines. I like colorful and simple business cards. My business is just getting started as I will be the only employee for now. I would like to be able to use the design on the card for my logo also. I don't know if logo design is a different service altogether.

If you can convince me to go with double-sided, then so be it, but until then, I'll stick with singe-sided.

Target Market(s)

busy families, health conscious, private parties, brunch parties, dinner parties

Industry/Entity Type

Chef

Contact Information for Business Card

Owen Talbot
owentalbot@kestrelmail.com
555-418-2937
Simmered Personal Chef Service
Serving the DC/VA/MD area

Font styles to use
Serif
Sans Serif
Decorative
Script
Other font styles liked:
• Anything

Requirements
Must have
• I will be using the illustration as my logo so that I can use it for promotional merchandise.

```html
<!DOCTYPE html>
<html lang="en">
<head>
<meta charset="utf-8">
<title>Simmered Personal Chef Service – Business Card</title>
<link href="https://fonts.googleapis.com/css2?family=Marcellus&family=Mulish:wght@400&display=swap" rel="stylesheet">
<style>
  :root {
    --backdrop: #ecebe8;
    --card-blue: #00b6ed;
    --badge-lime: #d9e356;
    --ink-white: #ffffff;
    --shadow: rgba(0, 0, 0, 0.18);
  }
  * { box-sizing: border-box; margin: 0; padding: 0; }
  html, body { width: 1200px; height: 1200px; overflow: hidden; }
  body {
    background: var(--backdrop);
    position: relative;
    font-family: "Mulish", sans-serif;
    color: var(--ink-white);
  }
  .card {
    position: absolute;
    left: 250px;
    width: 700px;
    height: 400px;
    background: var(--card-blue);
    box-shadow: 0 6px 18px var(--shadow);
    overflow: hidden;
  }
  .card--back { top: 150px; }
  .card--front { top: 650px; }

  .wordmark {
    position: absolute;
    display: flex;
    align-items: center;
    gap: 16px;
  }
  .wordmark__dot {
    width: 44px;
    height: 44px;
    border-radius: 50%;
    background: var(--badge-lime);
  }
  .wordmark__name {
    font-family: "Marcellus", serif;
    font-size: 46px;
    font-weight: 400;
    letter-spacing: 1px;
    color: var(--ink-white);
  }
  .card--back .wordmark { left: 50%; top: 105px; transform: translateX(-50%); }
  .card--front .wordmark { left: 48px; top: 170px; }

  .services {
    position: absolute;
    left: 0;
    right: 0;
    top: 265px;
    text-align: center;
    font-family: "Marcellus", serif;
    font-size: 27px;
    font-weight: 400;
    line-height: 1.3;
  }

  .contact {
    position: absolute;
    left: 372px;
    top: 132px;
  }
  .contact__name {
    font-family: "Marcellus", serif;
    font-size: 36px;
    font-weight: 400;
    margin-bottom: 22px;
  }
  .contact__line {
    font-size: 19px;
    line-height: 1.45;
  }
  .card__rules {
    position: absolute;
    inset: 0;
    width: 100%;
    height: 100%;
  }
</style>
</head>
<body>

  <section class="card card--back" aria-label="Card back">
    <div class="wordmark">
      <span class="wordmark__dot"></span>
      <span class="wordmark__name">Simmered</span>
    </div>
    <p class="services">
      Private parties • Intimate dinners<br>
      Brunch gatherings • Meal planning
    </p>
  </section>

  <section class="card card--front" aria-label="Card front">
    <svg class="card__rules" viewBox="0 0 700 400" aria-hidden="true">
      <line x1="700" y1="8" x2="605" y2="110" stroke="#ffffff" stroke-width="1.2" opacity="0.8"/>
      <line x1="700" y1="36" x2="650" y2="82" stroke="#ffffff" stroke-width="1.2" opacity="0.8"/>
      <line x1="370" y1="300" x2="300" y2="360" stroke="#ffffff" stroke-width="1.2" opacity="0.8"/>
    </svg>
    <div class="wordmark">
      <span class="wordmark__dot"></span>
      <span class="wordmark__name">Simmered</span>
    </div>
    <div class="contact">
      <h1 class="contact__name">Owen Talbot</h1>
      <p class="contact__line">555-418-2937</p>
      <p class="contact__line">owentalbot@kestrelmail.com</p>
      <p class="contact__line">Serving the DC Metro area</p>
    </div>
  </section>

</body>
</html>
```